Looking to Redesign Brevonix.com website

You guys did one of the brochures for brevonix.com and I would like to see if we can go ahead and get an estimate for a redesigned web site for the company. We currently have a couple of pages on brevonix.com which are very much a starter type site.

The new design will need to reflect some of the things discussed in the brochure. It will have flash. Needs to be designed for simple hosting using cpanels.

The site needs to have between 12 and 15 pages with flash pages to move through features. Integrated with twitter like it is now, and contact forms delivered from our CRM along with other interactive features such as subscription to newsletter, etc...

I don't have lots of details on how to proceed yet, but here are some competitor sites:

Can we take a look at potential costs involved in the redo of the site as vague as my description above can permit.

Target Market(s)

Business to Business

Number of Pages Required

5+ page

Font styles to use
Sans Serif

Requirements
Must have
• Must have professional feel. Similar to brochure. and logo.
• Include our story in the discussion.
• embedded links to our CRM for popup contact forms.
• Logo files and 2 types of brochures uploaded.
• Important to keep color scheme
Nice to have
• Flash and some movement
Should not have
• Not sure yet

```html
<!DOCTYPE html>
<html lang="en">
<head>
<meta charset="utf-8">
<title>Brevonix</title>
<link rel="stylesheet" href="https://fonts.googleapis.com/css2?family=Open+Sans:ital,wght@0,400;0,600;0,700;1,400&family=Russo+One&family=Arimo:wght@400;500&display=swap">
<style>
:root{
  --red:#b40000;
  --red-deep:#a00000;
  --ink:#1a1a1a;
  --text:#555;
  --muted:#777;
  --rule:#e3e3e3;
  --footer:#1d1d1d;
  --footer-base:#121212;
  --footer-text:#d8d8d8;
  --white:#fff;
}
*{margin:0;padding:0;box-sizing:border-box}
html,body{width:753px;height:1200px;overflow:hidden;background:var(--white)}
body{position:relative;font-family:"Open Sans",Arial,sans-serif;color:var(--text)}
.abs{position:absolute}
.topline{left:0;top:0;width:753px;height:2px;background:var(--red)}
.header{left:0;top:2px;width:753px;height:66px;background:var(--white);box-shadow:0 1px 3px rgba(0,0,0,.12);z-index:2}
.brand{left:102px;top:22px;display:flex;align-items:center;gap:6px;font:700 20px "Open Sans",sans-serif;color:var(--red)}
.brand .dot{width:22px;height:22px;border-radius:50%;background:var(--red)}
.call{left:408px;top:15px;font:500 10.5px "Arimo",sans-serif;color:#333;display:flex;align-items:center;gap:5px}
.call b{color:var(--red);font-weight:500}
.toplinks{left:556px;top:15px;font:400 8.5px "Arimo",sans-serif;color:var(--red);display:flex;gap:23px}
.nav{left:242px;top:44px;display:flex;gap:24px;font:400 7.6px "Arimo",sans-serif;color:#222;letter-spacing:.1px}
.nav .on{color:var(--red)}
.hero{left:0;top:68px;width:753px;height:285px;background:linear-gradient(90deg,#c9ccd3 0%,#aab0ba 40%,#7f8898 65%,#2d3646 100%)}
.hero-glow{left:640px;top:100px;width:90px;height:90px;border-radius:50%;background:radial-gradient(circle,rgba(255,190,90,.55),rgba(255,190,90,0) 70%)}
.hero h1{left:101px;top:158px;font:400 23px "Russo One",sans-serif;font-style:italic;color:var(--white)}
.hero-sub{left:101px;top:191px;width:240px;font:400 12px/15.5px "Arimo",sans-serif;color:var(--white)}
.btn{display:flex;align-items:center;justify-content:center;background:var(--red-deep);color:var(--white);border-radius:11px;font:700 6.4px "Open Sans",sans-serif;letter-spacing:.2px}
.dots{left:356px;top:318px;display:flex;gap:2px}
.dots i{width:9px;height:9px;border-radius:50%;background:var(--white);display:block}
.dots i.on{background:var(--red);border:1.5px solid var(--white)}
.features{left:0;top:353px;width:753px;height:195px;background:var(--red)}
.feature{top:17px;width:130px;margin-left:-65px;text-align:center;color:var(--white)}
.feature .ring{width:62px;height:62px;margin:0 auto;border:2px solid var(--white);border-radius:50%;display:flex;align-items:center;justify-content:center}
.feature h3{margin-top:16px;font:400 9.5px "Russo One",sans-serif;font-style:italic}
.feature p{margin-top:9px;font:400 7px/11.3px "Open Sans",sans-serif}
.feature a{display:block;margin-top:8px;font:700 7px "Open Sans",sans-serif;letter-spacing:.3px}
.section-title{font:400 13.5px "Russo One",sans-serif;font-style:italic;color:var(--ink)}
.section-title em{color:var(--red)}
.works-text{left:102px;top:631px;width:296px;font:400 6.6px/11.3px "Open Sans",sans-serif;color:#555}
.diagram{left:420px;top:576px;width:232px;height:182px;border:1px solid var(--rule);padding:3px;background:var(--white)}
.diagram div{width:100%;height:100%;background:linear-gradient(90deg,#eeeeea,#f6f4ec 50%,#ececea)}
.rule{height:1px;background:var(--rule)}
.news-img{width:75px;height:62px;border:2px solid #eee;background:linear-gradient(135deg,#9aa4b3,#56627a)}
.news-img.b{background:linear-gradient(135deg,#d8c9bf,#8a8f9a)}
.news-title{font:400 9px "Arimo",sans-serif;color:#222}
.news-text{width:190px;font:400 6.8px/11.3px "Open Sans",sans-serif;color:#555}
.meta{font:400 7px "Open Sans",sans-serif;color:var(--red)}
.avatar{width:48px;height:48px;border-radius:50%;border:3px solid #eee;background:radial-gradient(circle at 50% 45%,#d9b59a,#7a5a48)}
.quote{width:175px;font:italic 400 6.6px/11.6px "Open Sans",sans-serif;color:#666}
.quote b{font:700 12px "Russo One",sans-serif;color:var(--red);font-style:normal;margin-right:4px;vertical-align:-2px}
.cite{font:600 6.4px "Open Sans",sans-serif;color:var(--red)}
.footer{left:0;top:1022px;width:753px;height:140px;background:var(--footer)}
.footer-brand{left:102px;top:1084px;display:flex;align-items:center;gap:6px;font:700 20px "Open Sans",sans-serif;color:#777}
.footer-brand .dot{width:22px;height:22px;border-radius:50%;background:#777}
.fcol h4{font:400 8.5px "Russo One",sans-serif;font-style:italic;color:var(--white);margin-bottom:8px}
.fcol li{list-style:none;font:400 7.2px/14.2px "Open Sans",sans-serif;color:var(--footer-text)}
.vline{width:1px;background:#333}
.field{width:151px;height:20px;background:var(--white);border:1px solid #ccc;font:400 6.4px "Open Sans",sans-serif;color:#666;padding:6px 7px}
.signup{left:499px;top:1125px;width:63px;height:22px;background:var(--red);color:var(--white);font:700 8px "Open Sans",sans-serif;display:flex;align-items:center;justify-content:center;letter-spacing:.3px}
.base{left:0;top:1162px;width:753px;height:38px;background:var(--footer-base)}
.social{left:101px;top:1173px;display:flex;gap:3px}
.social i{width:16px;height:16px;border:1px solid #ddd;border-radius:50%;display:block}
.copy{left:491px;top:1177px;font:400 6.5px "Open Sans",sans-serif;color:#ccc}
</style>
</head>
<body>
<div class="abs topline"></div>
<header class="abs header">
  <div class="abs brand" style="top:20px"><span class="dot"></span>brevonix</div>
  <div class="abs call">
    <svg width="9" height="9" viewBox="0 0 24 24"><path fill="#b40000" d="M6.6 10.8a15.1 15.1 0 0 0 6.6 6.6l2.2-2.2c.3-.3.7-.4 1-.2 1.1.4 2.3.6 3.6.6.6 0 1 .4 1 1V20c0 .6-.4 1-1 1A17 17 0 0 1 3 4c0-.6.4-1 1-1h3.5c.6 0 1 .4 1 1 0 1.3.2 2.5.6 3.6.1.3 0 .7-.2 1z"/></svg>
    CALL US: <b>00-000-0412</b>
  </div>
  <div class="abs toplinks"><span>SUPPORT</span><span>CONTACT</span></div>
  <nav class="abs nav"><span class="on">HOME</span><span>ABOUT</span><span>WHY BREVONIX</span><span>FEATURES</span><span>ADVANTAGES</span><span>BEST OF CLASS HARDWARE</span></nav>
</header>

<section class="abs hero" role="img" aria-label="Photo of a businessman's hand touching a glowing network of connected people figures">
</section>
<div class="abs hero-glow"></div>
<h1 class="abs hero" style="background:none;height:auto;width:auto;left:101px;top:158px;font:400 23px 'Russo One',sans-serif;font-style:italic;color:#fff">About Brevonix</h1>
<p class="abs hero-sub">Sed ut perspiciatis unde omnienatus error sit voluptatemcusan tiumdolorem que lauda ntiumtotammpe riam</p>
<a class="abs btn" style="left:101px;top:250px;width:84px;height:20px">GET STARTED HERE</a>
<div class="abs dots"><i></i><i></i><i class="on"></i><i></i></div>

<section class="abs features">
  <div class="abs feature" style="left:158px">
    <div class="ring"><svg width="30" height="30" viewBox="0 0 30 30" fill="#fff"><circle cx="15" cy="7" r="3.5"/><path d="M9 15a6 4 0 0 1 12 0z"/><circle cx="8" cy="18" r="3"/><circle cx="22" cy="18" r="3"/><path d="M3 26a5 4 0 0 1 10 0zM17 26a5 4 0 0 1 10 0z"/><rect x="6" y="14" width="18" height="1.5"/></svg></div>
    <h3>Borum Malorm</h3>
    <p>Sed ut perspiciatis unde omniena tus error sit voluptatemcusan tium doloremque lauda ntium, totammpe riam, eaque ipsa uae ab illo in.</p>
    <a>READ MORE</a>
  </div>
  <div class="abs feature" style="left:303px">
    <div class="ring"><svg width="30" height="30" viewBox="0 0 30 30"><circle cx="15" cy="15" r="12" fill="#fff"/><path d="M8 9c3 1 4 4 2 6s1 4 3 3M17 5c-1 3 2 4 5 4M20 18c2 0 3 3 1 6" stroke="#b40000" stroke-width="2" fill="none"/></svg></div>
    <h3>Borum Malorm</h3>
    <p>Sed ut perspiciatis unde omniena tus error sit voluptatemcusan tium doloremque lauda ntium, totammpe riam, eaque ipsa uae ab illo in.</p>
    <a>READ MORE</a>
  </div>
  <div class="abs feature" style="left:448px">
    <div class="ring"><svg width="30" height="30" viewBox="0 0 30 30" fill="none" stroke="#fff" stroke-width="1.8"><rect x="5" y="4" width="10" height="20"/><path d="M7 8h6M7 12h6M7 16h6"/><rect x="14" y="14" width="12" height="8"/><path d="M20 22v4M16 26h8M17 9h6l-2-2M23 11h-6l2 2"/></svg></div>
    <h3>Borum Malorm</h3>
    <p>Sed ut perspiciatis unde omniena tus error sit voluptatemcusan tium doloremque lauda ntium, totammpe riam, eaque ipsa uae ab illo in.</p>
    <a>READ MORE</a>
  </div>
  <div class="abs feature" style="left:593px">
    <div class="ring"><svg width="30" height="30" viewBox="0 0 30 30" fill="none" stroke="#fff" stroke-width="1.8"><circle cx="15" cy="10" r="2" fill="#fff"/><path d="M15 12l-5 15M15 12l5 15M11 22h8M10 5a7 7 0 0 0 0 10M20 5a7 7 0 0 1 0 10M7 3a11 11 0 0 0 0 14M23 3a11 11 0 0 1 0 14"/></svg></div>
    <h3>Borum Malorm</h3>
    <p>Sed ut perspiciatis unde omniena tus error sit voluptatemcusan tium doloremque lauda ntium, totammpe riam, eaque ipsa uae ab illo in.</p>
    <a>READ MORE</a>
  </div>
</section>

<h2 class="abs section-title" style="left:102px;top:598px">How It <em>Works Brevonix</em></h2>
<p class="abs works-text">Sed ut perspiciatis unde omnis iste natus error sit voluptatem accusantium doloremque lauda ntium, totam rem aperiam, eaque ipsa quae ab illo inventore veritatis et quasi architecto bea tae vitae dicta sunt explicabo. Nemo enim ipsam voluptatem quia voluptas sit aspernatur aut odit aut fugit, sed quia consequuntur magni dolores eos qui ratione voluptatem sequi nesc iunt.que porro quisquam est, qui dolorem ipsum quia dolor sit amet, consectetur, adipis civel it, sed quia non numquam eius modi tempora incidunt ut labore et dolore magnam ali uam quaerat voluptatem enim ad minima venia.</p>
<a class="abs btn" style="left:101px;top:722px;width:84px;height:20px">GET STARTED HERE</a>
<div class="abs diagram"><div role="img" aria-label="Technical diagram of client offices connected over the internet to unified communication servers and redundant telephony providers"></div></div>

<div class="abs rule" style="left:102px;top:785px;width:550px"></div>

<h2 class="abs section-title" style="left:102px;top:810px">Latest <em>News</em></h2>
<div class="abs news-img" style="left:102px;top:844px" role="img" aria-label="Photo of a businessman using a tablet"></div>
<div class="abs news-title" style="left:191px;top:844px">At vero eos et accusamus et iusto</div>
<p class="abs news-text" style="left:191px;top:860px">At vero eos et accusamus et iusto odio dignissimqui blanditiis praesentium voluptatum deleniti atque corrupti quos dolores et quas molestias excepturi</p>
<div class="abs meta" style="left:191px;top:898px">▣ Apr 05 2016 &nbsp;● Comments</div>
<div class="abs news-img b" style="left:102px;top:926px" role="img" aria-label="Photo of hands typing on a laptop keyboard"></div>
<div class="abs news-title" style="left:191px;top:926px">At vero eos et accusamus et iusto</div>
<p class="abs news-text" style="left:191px;top:942px">At vero eos et accusamus et iusto odio dignissimqui blanditiis praesentium voluptatum deleniti atque corrupti quos dolores et quas molestias excepturi</p>
<div class="abs meta" style="left:191px;top:980px">▣ Apr 05 2016 &nbsp;● Comments</div>

<h2 class="abs section-title" style="left:419px;top:810px">Client <em>Testimonials</em></h2>
<div class="abs avatar" style="left:418px;top:848px" role="img" aria-label="Portrait photo of a smiling client"></div>
<p class="abs quote" style="left:478px;top:845px"><b>“</b>At vero eos et accusamus et iusto odio dignissimqui blanditiis praesentium voluptatum deleniti atquAt vero ee set accusamus et iusto odio dignis sim qui blan.</p>
<div class="abs cite" style="left:478px;top:888px">ALAN REYES,CITY NAME</div>
<div class="abs rule" style="left:419px;top:918px;width:233px"></div>
<div class="abs avatar" style="left:418px;top:938px" role="img" aria-label="Portrait photo of a smiling client"></div>
<p class="abs quote" style="left:478px;top:936px"><b>“</b>At vero eos et accusamus et iusto odio dignissimqui blanditiis praesentium voluptatum deleniti atquAt vero ee set accusamus et iusto odio dignis sim qu.</p>
<div class="abs cite" style="left:478px;top:979px">ALAN REYES,CITY NAME</div>

<footer class="abs footer"></footer>
<div class="abs footer-brand"><span class="dot"></span>brevonix</div>
<div class="abs fcol" style="left:256px;top:1039px">
  <h4>PRODUCTS</h4>
  <ul><li>Alandit sed nulla</li><li>In ullamcorper</li><li>Est eget tempor</li><li>Cursus neque</li><li>Consectetuer</li><li>Cursus neque</li></ul>
</div>
<div class="abs vline" style="left:346px;top:1054px;height:86px"></div>
<div class="abs fcol" style="left:379px;top:1039px">
  <h4>SUPPORT</h4>
  <ul><li>FAQs</li><li>Privacy Policy</li><li>Recommendations</li><li>Contact</li></ul>
</div>
<div class="abs vline" style="left:464px;top:1054px;height:86px"></div>
<div class="abs fcol" style="left:498px;top:1039px">
  <h4>NEWSLETTER SUBSCRIPTION</h4>
  <ul><li>Please sign up here for latest deals</li></ul>
</div>
<div class="abs field" style="left:499px;top:1072px">Name:</div>
<div class="abs field" style="left:499px;top:1098px">Email address</div>
<div class="abs signup">SIGN UP ⊙</div>

<div class="abs base"></div>
<div class="abs social"><i></i><i></i><i></i><i></i></div>
<div class="abs copy">Copyright © 2016 &nbsp;brevonix. - All rights reserved</div>
</body>
</html>
```